Upmarket Dessert Lounge needs a Business Card Design

We are an upmarket dessert lounge needing a business card to match our image.

We want something that is simple yet beautiful, feminine, classy, sophisticated and elegant. We want it to stand out and don't mind if it is bold.

The design should include our logo and colours of red or maroon with gold highlights. We don't mind if black is used.

Marlow & Quince

Target Market(s)

For those who like to indulge or treat themselves and give in to their temptations on good quality desserts.

Industry/Entity Type

Business

Requirements
Must have
• Must include our logo and our name

Marlow & Quince

M & Q

```html
<!DOCTYPE html>
<html lang="en">
<head>
<meta charset="utf-8">
<title>Marlow &amp; Quince — Business Card</title>
<link rel="stylesheet" href="https://fonts.googleapis.com/css2?family=Tinos:wght@400;700&display=swap">
<style>
  :root {
    --backdrop: #ece6de;
    --card-navy: #020c24;
    --gold: #edc98f;
    --ink-light: #f4f1ec;
    --ruby: #9a1e1e;
    --maroon: #8a1a1c;
    --divider: #9aa0ad;
  }
  * { box-sizing: border-box; margin: 0; padding: 0; }
  html, body {
    width: 1200px;
    height: 417px;
    overflow: hidden;
    background: var(--backdrop);
  }
  body {
    position: relative;
    font-family: "Tinos", "Times New Roman", serif;
  }
  .card {
    position: absolute;
    top: 62px;
    width: 515px;
    height: 293px;
    background: var(--card-navy);
    box-shadow: 0 2px 8px rgba(0,0,0,0.25);
  }
  .card--front { left: 55px; }
  .card--back { left: 630px; }

  .badge {
    position: absolute;
    left: 129px;
    width: 257px;
    height: 146px;
    border-radius: 40px;
    background: var(--maroon);
    display: flex;
    align-items: center;
    justify-content: center;
  }
  .card--front .badge { top: 30px; }
  .card--back .badge { top: 54px; }

  .brand-name {
    font-family: "Tinos", "Times New Roman", serif;
    font-weight: 400;
    font-size: 21px;
    letter-spacing: 0.5px;
    color: var(--gold);
    text-transform: uppercase;
    white-space: nowrap;
  }

  .holder {
    position: absolute;
    top: 204px;
    left: 0;
    width: 100%;
    text-align: center;
    color: var(--gold);
  }
  .holder__name { font-weight: 700; font-size: 17px; letter-spacing: 0.3px; }
  .holder__title { font-weight: 400; font-size: 14px; }

  .contact {
    position: absolute;
    top: 239px;
    font-size: 13px;
    line-height: 19px;
    color: var(--ink-light);
  }
  .contact--address { left: 40px; }
  .contact--phones { left: 183px; }
  .contact--online { left: 333px; }
  .contact__line { display: flex; align-items: center; white-space: nowrap; }
  .contact__icon { width: 9px; height: 9px; margin-right: 7px; flex: none; }

  .divider {
    position: absolute;
    top: 241px;
    width: 1px;
    height: 38px;
    background: var(--divider);
  }
  .divider--one { left: 168px; }
  .divider--two { left: 318px; }

  .web-address {
    position: absolute;
    top: 232px;
    left: 0;
    width: 100%;
    text-align: center;
    font-size: 13px;
    letter-spacing: 2.6px;
    color: var(--ink-light);
  }
</style>
</head>
<body>

<section class="card card--front">
  <div class="badge" role="img" aria-label="Ornamental maroon badge with gold flourishes framing the lounge name">
    <span class="brand-name">Marlow &amp; Quince</span>
  </div>

  <div class="holder">
    <span class="holder__name">YOUR NAME /</span>
    <span class="holder__title">Title</span>
  </div>

  <div class="contact contact--address">
    <div class="contact__line">00, Complex name</div>
    <div class="contact__line">City, State 000 000</div>
  </div>

  <div class="divider divider--one"></div>

  <div class="contact contact--phones">
    <div class="contact__line">
      <svg class="contact__icon" viewBox="0 0 10 10" aria-hidden="true">
        <path d="M2 1 L4 1 L4.6 3 L3.4 3.8 Q4.4 5.8 6.2 6.6 L7 5.4 L9 6 L9 8 Q8.6 9 7.6 9 Q1 8.4 1 2.4 Q1 1.4 2 1 Z" fill="var(--ruby)"/>
      </svg>+1 555 014 7781
    </div>
    <div class="contact__line">
      <svg class="contact__icon" viewBox="0 0 10 10" aria-hidden="true">
        <rect x="2.5" y="0.5" width="5" height="9" rx="1" fill="var(--ruby)"/>
        <rect x="3.4" y="1.6" width="3.2" height="5.4" fill="var(--card-navy)"/>
      </svg>+1 555 014 7781
    </div>
  </div>

  <div class="divider divider--two"></div>

  <div class="contact contact--online">
    <div class="contact__line">
      <svg class="contact__icon" viewBox="0 0 10 10" aria-hidden="true">
        <rect x="0.5" y="2" width="9" height="6" fill="var(--ruby)"/>
        <path d="M0.8 2.3 L5 5.6 L9.2 2.3" fill="none" stroke="var(--card-navy)" stroke-width="0.8"/>
      </svg>hello@mqlounge.com
    </div>
    <div class="contact__line">
      <svg class="contact__icon" viewBox="0 0 10 10" aria-hidden="true">
        <circle cx="5" cy="5" r="4.5" fill="var(--ruby)"/>
        <path d="M0.8 5 H9.2 M5 0.6 Q2.6 5 5 9.4 M5 0.6 Q7.4 5 5 9.4" fill="none" stroke="var(--card-navy)" stroke-width="0.6"/>
      </svg>www.marlowquince.com
    </div>
  </div>
</section>

<section class="card card--back">
  <div class="badge" role="img" aria-label="Ornamental maroon badge with gold flourishes framing the lounge name">
    <span class="brand-name">Marlow &amp; Quince</span>
  </div>
  <div class="web-address">www.marlowquince.com</div>
</section>

</body>
</html>
```